Revamp of existing namecard

Existingly, i've got a namecard that i would like to retain the main design. but there are some changes in my company and i would need to do some amendments to it.

We are a money transfer and money exchange company.
I need 2 different types of name card.
1. For individual name cards
the front to put the following:
Company name and logo
English Name, Chinese Name appointment
Mobile Number, Email and Website.
2 License number under the logo and name

the back of the name card to put
8 address: 7 Singapore and 1 Hong Kong branch addresses
8 Mobile Number of the corresponding addresses.

We would like to retain the name card front design
the name card back design can change but color to retain.

2nd name card is generic name card
Front:
Company name and logo
Branch Mobile Number, Branch Address, Email and Website.

Industry/Entity Type

remittance and money exchange

Contact Information for Business Card

I need 2 different types of name card. 1. For individual name cards the front to put the following: Company name and logo English Name, Chinese Name appointment Mobile Number, Email and Website. 2 License number under the logo and name the back of the name card to put 8 address: 7 Singapore and 1 Hong Kong branch addresses 8 Mobile Number of the corresponding addresses. We would like to retain the name card front design the name card back design can change but color to retain. 2nd name card is generic name card Front: the front to put the following: Company name and logo Branch Mobile Number, Branch Address, Email and Website. 2 License number under the logo and name

Requirements
Must have
• I need 2 different types of name card. 1. For individual name cards the front to put the following: Company name and logo English Name, Chinese Name appointment Mobile Number, Email and Website. 2 License number under the logo and name the back of the name card to put 8 address: 7 Singapore and 1 Hong Kong branch addresses 8 Mobile Number of the corresponding addresses. We would like to retain the name card front design the name card back design can change but color to retain. 2nd name card is generic name card Front: the front to put the following: Company name and logo Branch Mobile Number, Branch Address, Email and Website. 2 License number under the logo and name
Nice to have
• use back color code

```html
<!DOCTYPE html>
<html lang="en">
<head>
<meta charset="utf-8">
<title>Meridan name cards</title>
<link href="https://fonts.googleapis.com/css2?family=Montserrat:wght@400;500;600;700;800&family=Noto+Sans+SC:wght@500&display=swap" rel="stylesheet">
<style>
:root{
  --frame:#2f3541;
  --sheet:#ffffff;
  --card-dark:#28313d;
  --ink:#2b3340;
  --accent:#6cc3d5;
  --map-light:#eceef1;
  --map-dark:#1f2731;
  --guide:#2a2a2a;
}
*{margin:0;padding:0;box-sizing:border-box}
html,body{width:1175px;height:1200px;overflow:hidden;background:var(--frame)}
body{font-family:"Montserrat",sans-serif;color:var(--ink)}
.canvas{position:relative;width:1175px;height:1200px;background:var(--frame)}
.sheet{position:absolute;left:54px;top:69px;width:1064px;height:1064px;background:var(--sheet)}
.abs{position:absolute;white-space:nowrap;line-height:1}
.guides{position:absolute;left:0;top:0;z-index:1}
.set-title{font-size:40px;font-weight:500;transform:translateX(-50%);color:#111}
.side-label{font-size:30px;font-weight:400;transform:translateX(-50%);color:#111}
.card{position:absolute}
.card--dark{background:var(--card-dark);z-index:2}
.card--light{z-index:2}
.map{position:absolute}
.map--light{background:radial-gradient(ellipse at 50% 50%,var(--map-light) 0%,rgba(236,238,241,.5) 60%,rgba(255,255,255,0) 100%)}
.map--dark{background:radial-gradient(ellipse at 50% 50%,var(--map-dark) 0%,rgba(31,39,49,.5) 60%,rgba(40,49,61,0) 100%)}
.brand{font-weight:700;color:var(--ink);letter-spacing:.5px}
.brand--light{color:#fff}
.brand-mark{position:absolute;background:var(--accent)}
.license{font-weight:600;letter-spacing:1.6px;color:var(--ink)}
.person-name{font-size:20px;font-weight:700}
.person-name-zh{font-family:"Noto Sans SC",sans-serif;font-size:18px;font-weight:500}
.person-role{font-size:13px;font-weight:500;color:var(--accent)}
.contact{display:flex;align-items:center;gap:5px;font-size:11px;font-weight:700;color:var(--ink)}
.contact--phone{letter-spacing:2px}
.contact svg{width:10px;height:10px;flex:none}
.branch-title{display:flex;align-items:baseline;gap:3px;color:#fff;font-size:16px;font-weight:500;transform:translateX(-50%)}
.branch-title small{font-size:6px;color:var(--accent);font-weight:500}
.branch-title svg{width:9px;height:12px;align-self:center}
.branch-license{font-size:5.5px;font-weight:700;color:#fff;letter-spacing:.6px;transform:translateX(-50%)}
.outlet{transform:translateX(-50%);text-align:center}
.outlet-address{display:block;font-size:6.5px;color:#fff;padding-bottom:3px;border-bottom:.5px solid rgba(108,195,213,.6)}
.outlet-phone{display:block;font-size:6px;color:var(--accent);margin-top:6px}
.branch-label{font-size:11px;font-weight:500;color:var(--accent)}
.address{font-size:10.5px;font-weight:600;line-height:1.5}
.tagline{font-size:12px;font-weight:400;color:var(--accent)}
</style>
</head>
<body>
<div class="canvas">
  <div class="sheet"></div>

  <svg class="guides" width="1175" height="1200" viewBox="0 0 1175 1200" aria-hidden="true">
    <g stroke="var(--guide)" stroke-width="1" stroke-dasharray="6 6" fill="none">
      <line x1="108" y1="241" x2="108" y2="1000"/>
      <line x1="123" y1="241" x2="123" y2="1000"/>
      <line x1="550" y1="241" x2="550" y2="1000"/>
      <line x1="566" y1="241" x2="566" y2="1000"/>
      <line x1="618" y1="241" x2="618" y2="1000"/>
      <line x1="634" y1="241" x2="634" y2="1000"/>
      <line x1="1061" y1="241" x2="1061" y2="1000"/>
      <line x1="1077" y1="241" x2="1077" y2="1000"/>
      <line x1="65" y1="288" x2="1118" y2="288"/>
      <line x1="65" y1="305" x2="1118" y2="305"/>
      <line x1="65" y1="539" x2="1118" y2="539"/>
      <line x1="65" y1="557" x2="1118" y2="557"/>
      <line x1="65" y1="673" x2="1118" y2="673"/>
      <line x1="65" y1="690" x2="1118" y2="690"/>
      <line x1="65" y1="924" x2="1118" y2="924"/>
      <line x1="65" y1="942" x2="1118" y2="942"/>
    </g>
  </svg>

  <!-- Set 1 -->
  <div class="abs set-title" style="left:583px;top:168px">card 1</div>
  <div class="abs side-label" style="left:313px;top:234px">front</div>
  <div class="abs side-label" style="left:845px;top:234px">back</div>

  <!-- Set 1 front -->
  <div class="card card--light" style="left:108px;top:288px;width:458px;height:269px">
    <div class="map map--light" role="img" aria-label="Dotted world map in light grey" style="left:15px;top:28px;width:435px;height:210px"></div>
  </div>
  <div class="brand-mark" style="left:318px;top:322px;width:28px;height:28px;z-index:3"></div>
  <div class="abs brand" style="left:363px;top:319px;font-size:31px;z-index:3">MERIDAN</div>
  <div class="abs license" style="left:381px;top:346px;font-size:10.5px;z-index:3">04518820 | 04518821</div>

  <div class="abs person-name" style="left:133px;top:404px;z-index:3">Marcus Leung</div>
  <div class="abs person-name-zh" style="left:133px;top:424px;z-index:3">马可·梁</div>
  <div class="abs person-role" style="left:133px;top:447px;z-index:3">Director of Business Development</div>

  <div class="abs" style="left:364px;top:400px;z-index:3">
    <div class="contact contact--phone" style="height:18px"><svg viewBox="0 0 10 10"><rect x="2.5" y=".5" width="5" height="9" rx="1" fill="none" stroke="var(--accent)"/></svg>+852 5550 1234</div>
    <div class="contact contact--phone" style="height:18px"><svg viewBox="0 0 10 10"><path d="M2 1l2 2-1 1.3c.7 1.3 1.5 2.1 2.7 2.7L7 6l2 2-1.3 1.3C4.5 9 1 5.5.7 2.3z" fill="var(--accent)"/></svg>+852 5550 1234</div>
    <div class="contact" style="height:18px"><svg viewBox="0 0 10 10"><rect x=".5" y="2" width="9" height="6.5" fill="var(--accent)"/><path d="M.5 2L5 5.5 9.5 2" fill="none" stroke="#fff" stroke-width=".8"/></svg>marcus@meridan.com.hk</div>
    <div class="contact" style="height:18px"><svg viewBox="0 0 10 10"><circle cx="5" cy="5" r="4.5" fill="var(--accent)"/><path d="M.5 5h9M5 .5c-2.5 3-2.5 6 0 9M5 .5c2.5 3 2.5 6 0 9" fill="none" stroke="#fff" stroke-width=".6"/></svg>www.meridan.com.hk</div>
  </div>

  <!-- Set 1 back -->
  <div class="card card--dark" style="left:618px;top:288px;width:459px;height:269px">
    <div class="map map--dark" role="img" aria-label="Dotted world map in deep navy" style="left:14px;top:28px;width:430px;height:230px"></div>
  </div>
  <div style="position:absolute;left:0;top:0;z-index:3">
    <div class="abs branch-title" style="left:852px;top:306px"><svg viewBox="0 0 9 12"><path d="M4.5 0A4.5 4.5 0 0 0 0 4.5C0 8 4.5 12 4.5 12S9 8 9 4.5A4.5 4.5 0 0 0 4.5 0z" fill="var(--accent)"/><circle cx="4.5" cy="4.5" r="1.7" fill="var(--card-dark)"/></svg>Singapore<small>Branch</small></div>
    <div class="abs branch-license" style="left:850px;top:325px">04518820 | 04518821</div>

    <div class="abs outlet" style="left:746px;top:341px"><span class="outlet-address">Maple Court #01-00, 125 Linden Road, 204518</span><span class="outlet-phone">+65 5550 2200</span></div>
    <div class="abs outlet" style="left:944px;top:341px"><span class="outlet-address">Maple Court #01-00, 125 Linden Road, 204518</span><span class="outlet-phone">+65 5550 2200</span></div>
    <div class="abs outlet" style="left:746px;top:374px"><span class="outlet-address">Maple Court #01-00, 125 Linden Road, 204518</span><span class="outlet-phone">+65 5550 2200</span></div>
    <div class="abs outlet" style="left:944px;top:374px"><span class="outlet-address">Maple Court #01-00, 125 Linden Road, 204518</span><span class="outlet-phone">+65 5550 2200</span></div>
    <div class="abs outlet" style="left:746px;top:406px"><span class="outlet-address">Maple Court #01-00, 125 Linden Road, 204518</span><span class="outlet-phone">+65 5550 2200</span></div>
    <div class="abs outlet" style="left:944px;top:406px"><span class="outlet-address">Maple Court #01-00, 125 Linden Road, 204518</span><span class="outlet-phone">+65 5550 2200</span></div>
    <div class="abs outlet" style="left:851px;top:440px"><span class="outlet-address">Maple Court #01-00, 125 Linden Road, 204518</span><span class="outlet-phone">+65 5550 2200</span></div>

    <div class="abs branch-title" style="left:853px;top:477px"><svg viewBox="0 0 9 12"><path d="M4.5 0A4.5 4.5 0 0 0 0 4.5C0 8 4.5 12 4.5 12S9 8 9 4.5A4.5 4.5 0 0 0 4.5 0z" fill="var(--accent)"/><circle cx="4.5" cy="4.5" r="1.7" fill="var(--card-dark)"/></svg>Hong Kong<small>Branch</small></div>
    <div class="abs branch-license" style="left:853px;top:496px">04518820 | 04518821</div>
    <div class="abs outlet" style="left:853px;top:513px"><span class="outlet-address">Harbour View Tower 18/F, 12 Kingfisher Road, HK</span><span class="outlet-phone">+852 5550 1234</span></div>
  </div>

  <!-- Set 2 -->
  <div class="abs set-title" style="left:586px;top:592px">card 2</div>
  <div class="abs side-label" style="left:313px;top:632px">front</div>
  <div class="abs side-label" style="left:845px;top:632px">back</div>

  <!-- Set 2 front -->
  <div class="card card--light" style="left:108px;top:673px;width:458px;height:269px">
    <div class="map map--light" role="img" aria-label="Dotted world map in light grey" style="left:15px;top:28px;width:435px;height:210px"></div>
  </div>
  <div class="brand-mark" style="left:228px;top:734px;width:28px;height:28px;z-index:3"></div>
  <div class="abs brand" style="left:276px;top:730px;font-size:31px;z-index:3">MERIDAN</div>
  <div class="abs license" style="left:296px;top:758px;font-size:10.5px;z-index:3">04518820 | 04518821</div>

  <div class="abs person-name" style="left:154px;top:803px;z-index:3">Bedok Hill</div>
  <div class="abs branch-label" style="left:154px;top:823px;z-index:3">branch</div>
  <svg class="abs" style="left:131px;top:840px;z-index:3" width="11" height="14" viewBox="0 0 9 12" aria-hidden="true"><path d="M4.5 0A4.5 4.5 0 0 0 0 4.5C0 8 4.5 12 4.5 12S9 8 9 4.5A4.5 4.5 0 0 0 4.5 0z" fill="var(--accent)"/><circle cx="4.5" cy="4.5" r="1.7" fill="#fff"/></svg>
  <div class="abs address" style="left:150px;top:841px;z-index:3">Unit 1810, 18th Floor<br>Harbour View Tower<br>12 Kingfisher Road, Wan Chai</div>

  <div class="abs" style="left:373px;top:820px;z-index:3">
    <div class="contact contact--phone" style="height:18px"><svg viewBox="0 0 10 10"><rect x="2.5" y=".5" width="5" height="9" rx="1" fill="none" stroke="var(--accent)"/></svg>+852 5550 1234</div>
    <div class="contact contact--phone" style="height:18px"><svg viewBox="0 0 10 10"><path d="M2 1l2 2-1 1.3c.7 1.3 1.5 2.1 2.7 2.7L7 6l2 2-1.3 1.3C4.5 9 1 5.5.7 2.3z" fill="var(--accent)"/></svg>+852 5550 1234</div>
    <div class="contact" style="height:18px"><svg viewBox="0 0 10 10"><rect x=".5" y="2" width="9" height="6.5" fill="var(--accent)"/><path d="M.5 2L5 5.5 9.5 2" fill="none" stroke="#fff" stroke-width=".8"/></svg>marcus@meridan.com.hk</div>
    <div class="contact" style="height:18px"><svg viewBox="0 0 10 10"><circle cx="5" cy="5" r="4.5" fill="var(--accent)"/><path d="M.5 5h9M5 .5c-2.5 3-2.5 6 0 9M5 .5c2.5 3 2.5 6 0 9" fill="none" stroke="#fff" stroke-width=".6"/></svg>www.meridan.com.hk</div>
  </div>

  <!-- Set 2 back -->
  <div class="card card--dark" style="left:618px;top:673px;width:459px;height:269px">
    <div class="map map--dark" role="img" aria-label="Dotted world map in deep navy" style="left:14px;top:30px;width:430px;height:230px"></div>
  </div>
  <div class="brand-mark" style="left:740px;top:785px;width:30px;height:30px;z-index:3"></div>
  <div class="abs brand brand--light" style="left:791px;top:781px;font-size:31px;z-index:3">MERIDAN</div>
  <div class="abs tagline" style="left:793px;top:810px;z-index:3">remittance and money exchange</div>
</div>
</body>
</html>
```